Pain cream backed by Pro-Athletes "Glacier Ember"

Looking to revamp the label brand.
It's an all-natural pain gel. It heats then cools. Looking for a very sharp look that gets the point of the product use across.
Eveyrthing about the original label can be changed except for the text. It still needs to have the same information but can be any color, font whatever.,
I'll need pdf's and ai files of the design.
Label Size die line is attached.
Original Label is attached.

```html
<!DOCTYPE html>
<html lang="en">
<head>
<meta charset="utf-8">
<title>Glacier Ember – Label</title>
<link rel="stylesheet" href="https://fonts.googleapis.com/css2?family=Rubik:ital,wght@1,800&family=Oswald:wght@400&family=Archivo:wght@700&display=swap">
<style>
  :root {
    --backdrop: #f4f6f7;
    --label-top: #ffffff;
    --label-mid: #e6eef2;
    --label-bottom: #b9ceda;
    --frost-light: rgba(255,255,255,0.55);
    --frost-shade: rgba(140,170,188,0.35);
    --ink-navy: #23466f;
    --ink-blue: #0f6aa3;
    --ink-sky: #1f88c2;
  }
  * { margin: 0; padding: 0; box-sizing: border-box; }
  html, body {
    width: 1200px;
    height: 1200px;
    overflow: hidden;
    background: var(--backdrop);
  }
  .canvas {
    position: relative;
    width: 1200px;
    height: 1200px;
  }
  .label {
    position: absolute;
    left: 390px;
    top: 40px;
    width: 420px;
    height: 1120px;
    overflow: hidden;
    background: linear-gradient(180deg, var(--label-top) 0%, var(--label-top) 22%, var(--label-mid) 48%, var(--label-bottom) 100%);
    box-shadow: 0 6px 24px rgba(40,70,90,0.12);
  }
  .frost-texture {
    position: absolute;
    left: 0;
    right: 0;
    top: 420px;
    bottom: 0;
    background:
      radial-gradient(ellipse 70% 20% at 60% 40%, var(--frost-light), transparent 70%),
      radial-gradient(ellipse 80% 25% at 40% 70%, var(--frost-shade), transparent 70%),
      radial-gradient(ellipse 60% 18% at 70% 88%, var(--frost-light), transparent 70%);
  }
  .tagline {
    position: absolute;
    right: 44px;
    top: 64px;
    text-align: right;
    font-family: "Rubik", sans-serif;
    font-style: italic;
    font-weight: 800;
    font-size: 62px;
    line-height: 1.02;
    color: var(--ink-blue);
    letter-spacing: 0.5px;
  }
  .volume {
    position: absolute;
    right: 46px;
    top: 296px;
    font-family: "Oswald", sans-serif;
    font-weight: 400;
    font-size: 32px;
    color: var(--ink-navy);
  }
  .brand {
    position: absolute;
    left: 58px;
    bottom: 86px;
    display: flex;
    flex-direction: column;
    transform-origin: left bottom;
    transform: rotate(-90deg) translateY(100%);
    font-family: "Archivo", sans-serif;
    font-weight: 700;
    color: var(--ink-navy);
    white-space: nowrap;
  }
  .brand-primary {
    font-size: 108px;
    line-height: 0.95;
    letter-spacing: 2px;
  }
  .brand-secondary {
    font-size: 64px;
    line-height: 1;
    letter-spacing: 2px;
  }
</style>
</head>
<body>
  <main class="canvas">
    <section class="label">
      <div class="frost-texture" role="img" aria-label="Soft frosted ice brush texture in pale blue tones"></div>
      <h2 class="tagline">Gets You<br>Back<br>Up</h2>
      <p class="volume">100ml (3.2oz)</p>
      <h1 class="brand">
        <span class="brand-primary">GLACIER</span>
        <span class="brand-secondary">EMBER</span>
      </h1>
    </section>
  </main>
</body>
</html>
```